Brand Identity Stationary Package

Hello I'm looking for a full branding package for my Property Management Company. I have a logo but looking to have the following
Business Card
Email signature
Facebook cover photo
Letterhead (word.doc)
#10 Envelope
Pocket Folder - link to 9x12 pocket folder design specs https://www.printorbit-example.ca/marketing-materials/presentation-folders
would like everything to match and be brand identifiable. The company looks after residential properties/apartments and some commercial properties. Attached is a zip of the files.
For Business Card
Name: Gareth Lindqvist
Position: Operations Manager
Number: 1 (555) 384-2917
Email: Gareth@harborkey-example.ca
Website: Harborkey-example.ca
Property Management

```html
<!DOCTYPE html>
<html lang="en">
<head>
<meta charset="utf-8">
<title>Harborkey Property Management – #10 Envelope</title>
<link rel="stylesheet" href="https://fonts.googleapis.com/css2?family=Montserrat:wght@500;600&family=Source+Sans+3:wght@400&display=swap">
<style>
  :root {
    --brand-green: #80a641;
    --ink: #111111;
    --paper: #f2f1f1;
    --paper-light: #ffffff;
    --backdrop: #d1d0d0;
    --white: #ffffff;
  }
  * { box-sizing: border-box; margin: 0; padding: 0; }
  html, body {
    width: 1200px;
    height: 1050px;
    overflow: hidden;
    background: var(--backdrop);
  }
  .canvas {
    position: relative;
    width: 1200px;
    height: 1050px;
  }
  .envelope {
    position: absolute;
    left: 145px;
    width: 910px;
    height: 390px;
    background: radial-gradient(ellipse at 50% 55%, var(--paper-light) 0%, var(--paper) 70%);
    overflow: hidden;
  }
  .envelope--back { top: 105px; }
  .envelope--front { top: 555px; }

  .flap {
    position: absolute;
    inset: 0;
    width: 910px;
    height: 390px;
  }
  .wordmark {
    font-family: "Montserrat", sans-serif;
    font-weight: 600;
    letter-spacing: 4px;
    line-height: 1;
  }
  .tagline {
    font-family: "Montserrat", sans-serif;
    font-weight: 500;
    font-size: 11px;
    letter-spacing: 8.4px;
    line-height: 1;
  }
  .back-logo {
    position: absolute;
    top: 33px;
    left: 0;
    width: 910px;
    text-align: center;
    color: var(--white);
  }
  .back-logo .wordmark { font-size: 41px; }
  .back-logo .tagline { margin-top: 11px; padding-left: 8px; }

  .front-logo {
    position: absolute;
    top: 60px;
    left: 52px;
  }
  .front-logo .wordmark { font-size: 37px; color: var(--ink); }
  .front-logo .tagline { margin-top: 9px; color: var(--ink); letter-spacing: 8px; }

  .contact-list {
    position: absolute;
    top: 146px;
    left: 52px;
    list-style: none;
    font-family: "Source Sans 3", sans-serif;
    font-size: 20px;
    color: var(--ink);
  }
  .contact-list li {
    display: flex;
    align-items: center;
    height: 26px;
  }
  .contact-icon {
    width: 16px;
    height: 16px;
    margin-right: 13px;
    flex: none;
  }
  .wave {
    position: absolute;
    left: 0;
    top: 0;
    width: 910px;
    height: 390px;
  }
</style>
</head>
<body>
<div class="canvas">

  <section class="envelope envelope--back" aria-label="Envelope back">
    <svg class="flap" viewBox="0 0 910 390" aria-hidden="true">
      <path fill="var(--brand-green)" d="M0 0 H910 L885 90 Q872 130 830 131 H80 Q38 130 25 90 Z"/>
    </svg>
    <div class="back-logo">
      <div class="wordmark">HARBORKEY</div>
      <div class="tagline">PROPERTY MANAGEMENT</div>
    </div>
  </section>

  <section class="envelope envelope--front" aria-label="Envelope front">
    <div class="front-logo">
      <div class="wordmark">HARBORKEY</div>
      <div class="tagline">PROPERTY MANAGEMENT</div>
    </div>

    <ul class="contact-list">
      <li>
        <svg class="contact-icon" viewBox="0 0 16 16" aria-hidden="true">
          <path fill="var(--brand-green)" d="M1 6 Q8 1 15 6 L13 8 L11 6.5 H5 L3 8 Z"/>
          <rect x="3" y="8" width="10" height="6" rx="1" fill="var(--brand-green)"/>
        </svg>
        <span>1 (555) 384-2917</span>
      </li>
      <li>
        <svg class="contact-icon" viewBox="0 0 16 16" aria-hidden="true">
          <rect x="0.5" y="3" width="15" height="10" fill="var(--brand-green)"/>
          <path d="M0.5 3 L8 9 L15.5 3" fill="none" stroke="var(--white)" stroke-width="1.2"/>
        </svg>
        <span>Gareth@harborkey-example.ca</span>
      </li>
      <li>
        <svg class="contact-icon" viewBox="0 0 16 16" aria-hidden="true">
          <circle cx="8" cy="8" r="7.5" fill="var(--brand-green)"/>
          <path d="M4 4 Q7 5 6 8 Q4 9 5 12 M10 3 Q9 6 12 7 Q13 10 11 12" fill="none" stroke="var(--white)" stroke-width="1.3"/>
        </svg>
        <span>www.Harborkey-example.ca</span>
      </li>
    </ul>

    <svg class="wave" viewBox="0 0 910 390" aria-hidden="true">
      <path fill="var(--ink)" d="M0 297 C80 335 200 345 330 342 C520 338 700 306 790 304 C850 303 890 315 910 328 L910 330 C880 321 840 310 780 311 C660 314 500 345 330 349 C190 352 80 340 0 323 Z"/>
      <path fill="var(--brand-green)" d="M0 338 C90 355 200 360 330 355 C520 345 680 315 790 314 C850 314 890 325 910 332 L910 390 L0 390 Z"/>
    </svg>
  </section>

</div>
</body>
</html>
```